Professional & attention grabbing.

A business card design, front and back. I already have a logo I will attach, but I am open to something new as well.
Things to include:
Name:
Title:
Phone:
Email:
Wanting something that is professional but attention grabbing.
Also we do a lot of work using drones on natural gas pipelines (leading the future)if you want to include any of that. I'm open to ideas.
Target Market(s)
Natural gas transmission industry / greenhouse gas mitigation industry
Industry/Entity Type
Business
Colors
Designer to choose colors to be used in the design.
Look and feel
Each slider illustrates characteristics of the customer's brand and the style your logo design should communicate.

```html
<!DOCTYPE html>
<html lang="en">
<head>
<meta charset="utf-8">
<title>KV Field Inspections – Business Card</title>
<link href="https://fonts.googleapis.com/css2?family=Open+Sans:wght@400;700&display=swap" rel="stylesheet">
<style>
  :root {
    --backdrop: #4a3a2e;
    --card: #ffffff;
    --charcoal: #38383a;
    --brand-red: #c1272d;
    --slate: #6a6a6c;
    --ink: #111111;
  }
  * { margin: 0; padding: 0; box-sizing: border-box; }
  html, body { width: 1200px; height: 1135px; overflow: hidden; }
  body {
    background: var(--backdrop);
    font-family: "Open Sans", Arial, sans-serif;
    position: relative;
  }
  .card {
    position: absolute;
    left: 235px;
    width: 680px;
    height: 406px;
    background: var(--card);
    box-shadow: 0 10px 24px rgba(0,0,0,.35);
    overflow: hidden;
  }
  .card--front { top: 90px; }
  .card--back { top: 625px; }

  .strip { position: absolute; }
  .strip--charcoal { background: var(--charcoal); }
  .strip--red { background: var(--brand-red); }
  .strip--slate { background: var(--slate); }

  .contact-icon {
    position: absolute;
    left: 34px;
    width: 22px;
    height: 22px;
    fill: #fff;
  }
  .holder-name {
    position: absolute;
    left: 80px;
    top: 56px;
    font-size: 27px;
    font-weight: 700;
    color: var(--ink);
    line-height: 1;
  }
  .holder-title {
    position: absolute;
    left: 80px;
    top: 89px;
    font-size: 13px;
    color: var(--ink);
  }
  .contact-text {
    position: absolute;
    left: 80px;
    font-size: 14px;
    color: var(--ink);
  }

  .wordmark {
    position: absolute;
    display: flex;
    align-items: center;
    color: var(--charcoal);
    font-weight: 700;
  }
  .wordmark__square { background: var(--brand-red); flex: none; }
  .wordmark__name { display: flex; flex-direction: column; line-height: 1; }
  .wordmark--front { left: 376px; top: 164px; gap: 12px; }
  .wordmark--front .wordmark__square { width: 50px; height: 50px; }
  .wordmark--front .wordmark__initials { font-size: 54px; letter-spacing: -1px; }
  .wordmark--front .wordmark__rest { font-size: 10px; letter-spacing: .3px; margin-top: 4px; }
  .wordmark--back { left: 186px; top: 147px; gap: 18px; }
  .wordmark--back .wordmark__square { width: 72px; height: 72px; }
  .wordmark--back .wordmark__initials { font-size: 80px; letter-spacing: -2px; }
  .wordmark--back .wordmark__rest { font-size: 13px; letter-spacing: .4px; margin-top: 6px; }
</style>
</head>
<body>

<section class="card card--front" aria-label="Card front">
  <div class="strip strip--charcoal" style="left:0;top:0;width:66px;height:101px"></div>
  <div class="strip strip--red" style="left:0;top:151px;width:66px;height:102px"></div>
  <div class="strip strip--slate" style="left:0;top:304px;width:66px;height:102px"></div>

  <div class="strip strip--charcoal" style="right:0;top:0;width:34px;height:65px"></div>
  <div class="strip strip--red" style="right:0;top:171px;width:34px;height:64px"></div>
  <div class="strip strip--slate" style="right:0;top:341px;width:34px;height:65px"></div>

  <svg class="contact-icon" style="top:52px" viewBox="0 0 24 24" aria-hidden="true">
    <circle cx="12" cy="8" r="4.5"/><path d="M3 21c0-4.5 4-7 9-7s9 2.5 9 7z"/>
  </svg>
  <p class="holder-name">Your Name</p>
  <p class="holder-title">Title</p>

  <svg class="contact-icon" style="top:215px" viewBox="0 0 24 24" aria-hidden="true">
    <path d="M6.6 10.8a15 15 0 0 0 6.6 6.6l2.2-2.2a1 1 0 0 1 1-.25 11.4 11.4 0 0 0 3.6.57 1 1 0 0 1 1 1V20a1 1 0 0 1-1 1A17 17 0 0 1 3 4a1 1 0 0 1 1-1h3.5a1 1 0 0 1 1 1c0 1.25.2 2.45.57 3.6a1 1 0 0 1-.25 1z"/>
  </svg>
  <p class="contact-text" style="top:214px">555 018 274</p>

  <svg class="contact-icon" style="top:361px" viewBox="0 0 24 24" aria-hidden="true">
    <path d="M2 5h20v14H2z" fill="none" stroke="#fff" stroke-width="1.6"/>
    <path d="M2 5l10 8 10-8" fill="none" stroke="#fff" stroke-width="1.6"/>
  </svg>
  <p class="contact-text" style="top:360px">name@kvfield.com</p>

  <div class="wordmark wordmark--front">
    <span class="wordmark__square"></span>
    <span class="wordmark__name">
      <span class="wordmark__initials">KV</span>
      <span class="wordmark__rest">FIELD INSPECTIONS</span>
    </span>
  </div>
</section>

<section class="card card--back" aria-label="Card back">
  <div class="strip strip--charcoal" style="left:0;top:96px;width:45px;height:71px"></div>
  <div class="strip strip--red" style="left:0;top:167px;width:45px;height:73px"></div>
  <div class="strip strip--slate" style="left:0;top:240px;width:45px;height:70px"></div>

  <div class="strip strip--charcoal" style="right:0;top:96px;width:47px;height:71px"></div>
  <div class="strip strip--red" style="right:0;top:167px;width:47px;height:73px"></div>
  <div class="strip strip--slate" style="right:0;top:240px;width:47px;height:70px"></div>

  <div class="wordmark wordmark--back">
    <span class="wordmark__square"></span>
    <span class="wordmark__name">
      <span class="wordmark__initials">KV</span>
      <span class="wordmark__rest">FIELD INSPECTIONS</span>
    </span>
  </div>
</section>

</body>
</html>
```